Business Card Design

Need a new business card to represent our legal vertical focus. attached is an example of our old business card and newest logo. we would like the card to also identify "Legal Tech" as a tag line of business.

Our new address is
4817 Marlowe Hatchfield Rd.
Suite 518
Cincinnati, OH 45917

we no longer have a fax number.

Target Market(s)

Tech Consulting for Law Firms

Industry/Entity Type

Legal

Contact Information for Business Card

should use logo and colors. we are a b2b company

Font styles to use
Other font styles liked:
• tahoma

Requirements
Must have
• all print should be in lower case just as shown in photos. tag line should not
Should not have
• pinstripes or drop shadows

```html
<!DOCTYPE html>
<html lang="en">
<head>
<meta charset="utf-8">
<title>CoilPath Legal Tech – Business Card</title>
<link rel="stylesheet" href="https://fonts.googleapis.com/css2?family=PT+Sans:wght@400;700&display=swap">
<style>
  :root {
    --backdrop: #2b2b2d;
    --card-white: #ffffff;
    --card-black: #0b0b0c;
    --navy: #2a3a8f;
    --orange: #e8531f;
    --grey: #6d6d6f;
    --ink: #3a3a3c;
  }
  * { box-sizing: border-box; margin: 0; padding: 0; }
  html, body {
    width: 1200px; height: 900px; overflow: hidden;
    background: var(--backdrop);
    font-family: "PT Sans", Tahoma, sans-serif;
  }
  .stage {
    position: relative; width: 1200px; height: 900px;
    display: flex; align-items: center; justify-content: center; gap: 60px;
  }
  .card {
    position: relative; width: 330px; height: 570px;
    border-radius: 16px; overflow: hidden;
  }
  .card--front { background: var(--card-white); }
  .card--back {
    background: var(--card-black);
    display: flex; flex-direction: column; align-items: center; justify-content: center;
  }
  .brand { position: absolute; left: 50px; top: 96px; }
  .brand__name {
    font-weight: 700; font-size: 40px; line-height: 1; color: var(--navy);
    display: flex; align-items: center; gap: 10px;
  }
  .brand__mark { width: 14px; height: 14px; background: var(--orange); border-radius: 50%; }
  .brand__tagline {
    margin-top: 4px; margin-left: 24px;
    font-size: 21px; letter-spacing: 4px; color: var(--grey);
  }
  .card--back .brand { position: static; }
  .card--back .brand__name { font-size: 36px; }
  .card--back .brand__tagline { color: #8a8a8c; font-size: 19px; }

  .rule { position: absolute; left: 40px; right: 40px; height: 2px; background: var(--orange); }
  .rule--top { top: 292px; }
  .rule--mid { top: 356px; }
  .person { position: absolute; left: 40px; top: 300px; }
  .person__name { font-size: 25px; color: var(--navy); line-height: 1.05; }
  .person__title { font-size: 15px; color: var(--ink); }
  .address { position: absolute; left: 40px; top: 372px; font-size: 14px; color: var(--ink); line-height: 1.35; }
  .contacts { position: absolute; left: 40px; top: 430px; list-style: none; }
  .contacts__item {
    display: flex; align-items: center; gap: 14px;
    font-size: 14px; color: var(--ink); height: 24px;
  }
  .contacts__icon { width: 16px; height: 16px; }
  .band { position: absolute; }
  .band--navy { left: 0; bottom: 34px; width: 210px; height: 10px; background: var(--navy); }
  .band--orange { right: 0; bottom: 46px; width: 110px; height: 12px; background: var(--orange); }
  .band--base { left: 0; bottom: 0; width: 100%; height: 8px; background: var(--navy); }
</style>
</head>
<body>
<main class="stage">
  <section class="card card--front" aria-label="Card front">
    <div class="brand">
      <div class="brand__name"><span class="brand__mark"></span>CoilPath</div>
      <div class="brand__tagline">Legal Tech</div>
    </div>
    <div class="person">
      <p class="person__name">martin l. doyle jr.</p>
      <p class="person__title">president &amp; virtual cio</p>
    </div>
    <div class="rule rule--top" style="top:294px;height:0"></div>
    <div class="rule rule--mid"></div>
    <address class="address" style="font-style:normal">
      4817 Marlowe Hatchfield Rd.<br>
      Suite 518 Cincinnati, OH 45917
    </address>
    <ul class="contacts">
      <li class="contacts__item">
        <svg class="contacts__icon" viewBox="0 0 16 16"><circle cx="8" cy="8" r="8" fill="#e8531f"/><path d="M5.2 4.2l1.4 1.6-.8 1c.6 1.2 1.4 2 2.6 2.6l1-.8 1.6 1.4-.8 1.3C7.8 11 5 8.2 4.2 5z" fill="#fff"/></svg>
        513.555.0148
      </li>
      <li class="contacts__item">
        <svg class="contacts__icon" viewBox="0 0 16 16"><circle cx="8" cy="8" r="8" fill="#e8531f"/><rect x="4" y="5.2" width="8" height="5.6" fill="#fff"/><path d="M4 5.2l4 3 4-3" stroke="#e8531f" stroke-width=".9" fill="none"/></svg>
        mdoyle@coilpath.net
      </li>
      <li class="contacts__item">
        <svg class="contacts__icon" viewBox="0 0 16 16"><circle cx="8" cy="8" r="8" fill="#e8531f"/><circle cx="8" cy="8" r="3.8" stroke="#fff" stroke-width="1" fill="none"/><ellipse cx="8" cy="8" rx="1.6" ry="3.8" stroke="#fff" stroke-width=".8" fill="none"/><path d="M4.2 8h7.6" stroke="#fff" stroke-width=".8"/></svg>
        www.coilpath.net
      </li>
    </ul>
    <div class="band band--orange"></div>
    <div class="band band--navy"></div>
    <div class="band band--base"></div>
  </section>

  <section class="card card--back" aria-label="Card back">
    <div class="brand">
      <div class="brand__name"><span class="brand__mark"></span>CoilPath</div>
      <div class="brand__tagline">Legal Tech</div>
    </div>
  </section>
</main>
</body>
</html>
```